Every Shelf Set Neatly or ESN Organized needs a business card design. ESN Organized is a professi

We need a business card design that is clean, sharp and conveys a sense of organization. I already have a logo.

Target Market(s)

Families (specifically mothers), small business owners, parents, seniors

Industry/Entity Type

Business

Contact Information for Business Card

My website is www.esnorganized-example.com and my Facebook page is http://www.sociallink-example.com/everyshelfsetneatly. The phone number is 418-552-7094 and I want to be listed as Lorna M. Pelham, Owner

Requirements
Must have
• My logo.

```html
<!DOCTYPE html>
<html lang="en">
<head>
<meta charset="utf-8">
<title>Every Shelf Set Neatly – Business Card</title>
<link rel="stylesheet" href="https://fonts.googleapis.com/css2?family=Open+Sans:wght@400;600;700&display=swap">
<style>
  :root {
    --brand-blue: #1a78d8;
    --ink: #111111;
    --paper: #ffffff;
    --stage: #ecedef;
    --text-dark: #222222;
  }
  * { box-sizing: border-box; margin: 0; padding: 0; }
  html, body { width: 1200px; height: 900px; overflow: hidden; }
  body {
    position: relative;
    background: var(--stage);
    font-family: "Open Sans", Arial, sans-serif;
  }
  .card {
    position: absolute;
    overflow: hidden;
    box-shadow: 0 4px 14px rgba(0,0,0,0.18);
  }

  /* Front */
  .card-front {
    left: 77px; top: 33px;
    width: 588px; height: 365px;
    background: var(--paper);
  }
  .card-front .bands { position: absolute; inset: 0; }
  .business-name {
    position: absolute;
    left: 0; right: 0; top: 84px;
    text-align: center;
    font-weight: 600;
    font-size: 34px;
    line-height: 44px;
    color: var(--text-dark);
  }
  .contact-list {
    position: absolute;
    right: 300px; top: 251px;
    list-style: none;
    text-align: right;
    color: var(--paper);
    font-size: 15px;
    line-height: 24px;
  }
  .contact-list li { display: flex; justify-content: flex-end; align-items: center; gap: 7px; }
  .contact-list svg { width: 12px; height: 12px; fill: var(--paper); flex: none; }
  .divider {
    position: absolute;
    left: 309px; top: 255px;
    width: 2px; height: 68px;
    background: var(--paper);
  }
  .person {
    position: absolute;
    left: 334px; top: 263px;
    color: var(--paper);
  }
  .person-name { font-weight: 700; font-size: 21px; line-height: 28px; }
  .person-role { font-size: 15px; line-height: 20px; }

  /* Back */
  .card-back {
    left: 388px; top: 505px;
    width: 567px; height: 352px;
    background: var(--brand-blue);
  }
  .back-name {
    position: absolute;
    left: 0; right: 0; top: 148px;
    text-align: center;
    font-weight: 600;
    font-size: 30px;
    line-height: 40px;
    color: var(--paper);
  }
  .social-band {
    position: absolute;
    left: 0; right: 0; top: 265px;
    height: 43px;
    background: var(--paper);
    display: flex; align-items: center; justify-content: center;
    color: var(--brand-blue);
    font-weight: 700;
    font-size: 14px;
  }
</style>
</head>
<body>

<section class="card card-front" aria-label="Business card front">
  <svg class="bands" width="588" height="365" viewBox="0 0 588 365" aria-hidden="true">
    <polygon points="0,201 396,201 374,227 0,227" fill="var(--ink)"/>
    <polygon points="0,231 386,231 416,193 588,193 588,365 0,365" fill="var(--brand-blue)"/>
  </svg>

  <p class="business-name">Every Shelf Set Neatly</p>

  <ul class="contact-list">
    <li>418-552-7094
      <svg viewBox="0 0 24 24" aria-hidden="true"><path d="M6.6 10.8a15 15 0 0 0 6.6 6.6l2.2-2.2c.3-.3.7-.4 1-.2 1.1.4 2.3.6 3.6.6.6 0 1 .4 1 1V20c0 .6-.4 1-1 1A17 17 0 0 1 3 4c0-.6.4-1 1-1h3.5c.6 0 1 .4 1 1 0 1.3.2 2.5.6 3.6.1.3 0 .7-.2 1z"/></svg>
    </li>
    <li>info@esnorganized-example.com
      <svg viewBox="0 0 24 24" aria-hidden="true"><path d="M2 5h20v14H2z M4 7v.5l8 5 8-5V7l-8 5z" fill-rule="evenodd"/></svg>
    </li>
    <li>www.esnorganized-example.com
      <svg viewBox="0 0 24 24" aria-hidden="true"><circle cx="12" cy="12" r="10"/></svg>
    </li>
  </ul>

  <div class="divider"></div>

  <div class="person">
    <p class="person-name">Lorna M. Pelham</p>
    <p class="person-role">Owner</p>
  </div>
</section>

<section class="card card-back" aria-label="Business card back">
  <p class="back-name">Every Shelf Set Neatly</p>
  <div class="social-band">www.sociallink-example.com/everyshelfsetneatly</div>
</section>

</body>
</html>
```